WEDDING ENTERTAINMENT COMPANY NEEDS ONE PAGE PSD web design + business card design

Dear Designers,
'T.O.R.U Entertainment' is a professional Sydney-based company that provides Master of Ceremonies and DJ services at wedding receptions.
We're after an adaptive single page web design (with scroll up & down pages), and a business card design.
The site should be fully compatible with mobile devices. I need the design layouts for computer, tablets and mobile phone.
"Our mission is to rid the earth of boring weddings!", so our website should reflect this philosophy.
The final design should communicate that we're FUN and easy-going MC and DJ duet.
IMPORTANT:
1. We would like to see creative and fun-looking designs - not the average looking templates (like the ones Kettle Forge or other sites offer).
2. We want our site to have a vertical rhythm, fun and creative layout with clip-art illustrations, and cute little details like little drawings e.g. hearts, flowers, birds, bride and groom, etc...
Example of a website: http://sun-over-the-bay.fenrudo.net/#en
https://the-garden-party.lopreni.com/home-layouts/home-2/
A website similar in style to this illustration (also attached): http://thumb4.pictovelle.com/display_pic_with_logo/5817302/382904157/stock-vector-wedding-invitation-design-template-cartoon-pigeons-bride-groom-on-retro-bicycle-floral-frame-and-382904157.jpg
We'd like to see designs that use the color PINK, combined with the other most popular wedding colors for example: gold, turquoise or light blue. We'll leave it up to you.
The site should also work with the attached logo.
NOTE: We attached the doc with the page content:
-Buttons/links
-Sections
-Text for each section
-Notes for the designers (in YELLOW).
If you have any questions, please don't be shy to ask. ;)
Happy creating, and we're looking forward to seeing your designs!
Thanks,
R & L
Target Market(s)
Couples getting married
Industry/Entity Type
Wedding
Contact Information for Business Card
The business card design should be based on the website design - colors, style etc.
FRONT SIDE:
1). Logo 2). Our contact details (to be provided)
BACK SIDE:
1). Logo 2). Our mission: 'Let's rid the earth of boring weddings!' 3). Services: 'Wedding MC | Wedding DJ | Extensive Party Pre-Planning | State of the Orin Music & Sound Equipment'
Number of Pages Required
1 page
Requirements
Must have
- IMPORTANT: Please send high res and full screen designs - so that we can see how the site will look like full screen.
- The site should work with the attached logo.
- Color PINK, combined with the other most popular wedding colors for example: gold, turquoise or light blue.
- IMPORTANT:
- 1. We would like to see creative and fun-looking designs - not the average looking templates (like the ones Kettle Forge or other sites offer).
- 2. We want our site to have a vertical rhythm, fun and creative layout with clip-art illustrations, and cute little details like little drawings e.g. hearts, flowers, birds, bride and groom, etc...
- Example of the website: http://sun-over-the-bay.fenrudo.net/#en
- https://the-garden-party.lopreni.com/home-layouts/home-2/
- A website similar in style to this illustration (attached):
- http://thumb4.pictovelle.com/display_pic_with_logo/5817302/382904157/stock-vector-wedding-invitation-design-template-cartoon-pigeons-bride-groom-on-retro-bicycle-floral-frame-and-382904157.jpg
Should not have
- No stock images/photos, only unique graphics, drawings, clip art illustrations

```html
<!DOCTYPE html>
<html lang="en">
<head>
<meta charset="utf-8">
<title>T.O.R.U Entertainment</title>
<link href="https://fonts.googleapis.com/css2?family=Open+Sans:ital,wght@0,400;0,600;0,700;1,400&family=Raleway:wght@400;600;700&display=swap" rel="stylesheet">
<style>
:root{
  --pink:#e0478d;
  --gold:#c9a227;
  --turq:#4dc3cd;
  --dark:#2b2b2b;
  --text:#555;
  --white:#fff;
  --light:#f6f3ef;
  --accent-yellow:#f7e26b;
}
*{margin:0;padding:0;box-sizing:border-box}
html,body{width:1200px;height:4932px;overflow:hidden}
body{font-family:'Open Sans',Arial,sans-serif;color:var(--text);background:var(--white);position:relative}
section,header,footer{position:absolute;left:0;width:1200px}
.abs{position:absolute}
.title{font-family:'Raleway',Arial,sans-serif;font-weight:600;letter-spacing:2px;text-align:center;width:100%;font-size:34px;color:var(--dark)}
.readmore{font-size:12px;font-weight:700;color:var(--gold);letter-spacing:1px;text-align:center}

/* header */
.site-header{top:0;height:92px;background:var(--white);border-top:4px solid var(--turq)}
.brand{left:60px;top:18px;display:flex;align-items:center;gap:10px}
.brand-dot{width:44px;height:44px;border-radius:50%;background:var(--dark)}
.brand-name{font-family:'Raleway',sans-serif;font-weight:700;font-size:14px;color:var(--dark);letter-spacing:1px}
.nav{right:60px;top:38px;display:flex;gap:22px;font-size:13px;font-weight:600;color:var(--dark);align-items:center}
.nav .active{color:var(--gold)}

/* hero */
.hero{top:92px;height:474px;background:linear-gradient(120deg,#6b3f7d,#c7738f 45%,#efc4b4 60%,#5a3a6a)}
.hero h1{position:absolute;top:245px;width:100%;text-align:center;font-family:'Raleway',sans-serif;font-weight:700;font-size:44px;color:var(--white)}
.hero p{position:absolute;top:315px;width:100%;text-align:center;color:var(--white);font-size:16px;line-height:24px}
.arrow{position:absolute;width:30px;height:30px}

/* what we do */
.what{top:566px;height:608px}
.service{position:absolute;top:141px;width:300px;text-align:center}
.service-circle{width:300px;height:300px;border-radius:50%;position:relative;overflow:hidden}
.service-band{position:absolute;left:0;right:0;top:175px;height:38px;line-height:38px;color:var(--white);font-size:15px;font-weight:600}
.service p{margin:22px 20px 0;font-size:12px;line-height:19px}
.service .readmore{margin-top:14px}

/* about */
.about{top:1174px;height:537px;background:linear-gradient(180deg,#4b2f22,#8c5a3e 55%,#d79c6c)}
.about-title{top:48px;color:var(--white)}
.about-lead{top:104px;left:400px;width:400px;text-align:center;color:var(--white);font-size:13px;line-height:20px}
.person{position:absolute;top:120px;width:320px}
.person h3{font-family:'Raleway',sans-serif;font-size:26px;color:var(--dark);font-weight:600;margin-bottom:14px}
.person p{font-size:12px;line-height:19px;margin-bottom:14px}
.portrait{position:absolute;top:190px;width:150px;height:150px;border-radius:50%;border:5px solid var(--white)}

/* why */
.why{top:1711px;height:467px}
.why-sub{top:100px;width:100%;text-align:center;color:var(--pink);font-weight:600;font-size:14px;letter-spacing:1px}
.reason{position:absolute;top:205px;width:230px;text-align:center}
.reason .icon{width:100px;height:100px;margin:0 auto;display:block}
.reason h4{font-size:18px;font-weight:600;color:var(--dark);margin:10px 0 8px}
.reason p{font-size:12px;line-height:19px}
.reason .readmore{margin-top:8px}
.ring{position:absolute;width:38px;height:38px;border-radius:50%;background:#e7e7e7}

/* couples */
.couples{top:2178px;height:464px;background:linear-gradient(120deg,#a98a2f,#c9ad55 50%,#9e8030)}
.couples .title{top:70px;color:var(--white)}
.avatar{left:550px;top:135px;width:100px;height:100px;border-radius:50%;border:4px solid var(--white);background:linear-gradient(#d9c3a4,#8a6d52)}
.quote{top:262px;left:220px;width:760px;text-align:center;color:var(--white);font-size:15px;font-style:italic;line-height:25px}
.signed{top:385px;width:100%;text-align:center;color:var(--white);font-weight:700;font-size:15px;letter-spacing:1px}

/* gallery */
.gallery{top:2642px;height:806px}
.gallery .title{top:60px}
.tile{position:absolute;width:328px}
.btn-outline{left:520px;top:712px;width:160px;height:40px;border:2px solid var(--gold);color:var(--gold);font-size:12px;font-weight:700;text-align:center;line-height:36px;letter-spacing:1px}

/* quote */
.instant{top:3448px;height:523px;background:var(--pink)}
.instant .title{top:55px;color:var(--white)}
.includes{left:100px;top:135px;width:540px;color:var(--white)}
.includes h5{font-size:15px;font-weight:700;margin-bottom:16px;letter-spacing:1px}
.includes li{list-style:none;font-size:12px;line-height:30px;display:flex;align-items:center;gap:12px}
.tick{width:16px;height:16px;flex:none}
.form-box{left:680px;top:122px;width:422px;height:345px;background:var(--white);padding:30px 40px}
.form-box h5{text-align:center;font-size:17px;color:var(--dark);font-weight:700;letter-spacing:1px;border-bottom:1px solid #ddd;padding-bottom:14px;margin-bottom:24px}
.field{display:flex;align-items:center;justify-content:space-between;margin-bottom:20px;font-size:12px;color:var(--dark)}
.select{width:230px;height:34px;border:1px solid #ccc;position:relative}
.select::after{content:"";position:absolute;right:0;top:0;width:28px;height:32px;background:#ddd}
.btn-gold{height:50px;background:var(--gold);color:var(--white);font-weight:700;font-size:14px;text-align:center;line-height:50px;letter-spacing:1px;margin-top:10px}

/* contact */
.contact{top:3971px;height:553px;background:var(--turq)}
.contact .title{top:55px;color:var(--white)}
.contact-info{left:100px;top:160px;width:520px;color:var(--white);font-size:13px;line-height:22px}
.contact-info b{display:block;margin-bottom:14px}
.contact-info .phone{color:var(--accent-yellow);font-weight:700}
.contact-line{display:flex;gap:40px;margin:18px 0}
.contact-line span{display:flex;align-items:center;gap:8px}
.contact-line i{width:14px;height:14px;background:var(--accent-yellow);border-radius:3px;display:inline-block}
.contact-form{left:690px;top:140px;width:412px;color:var(--white);font-size:12px}
.contact-form label{display:block;margin-bottom:4px}
.contact-form .input{height:34px;background:var(--white);margin-bottom:12px}
.contact-form .area{height:60px;background:var(--white)}
.send{right:0;top:0;width:60px;height:30px;background:var(--gold);color:var(--white);font-weight:700;font-size:12px;text-align:center;line-height:30px}

/* friends */
.friends{top:4524px;height:329px}
.friends .title{top:60px}
.friend{position:absolute;top:140px;width:320px;text-align:center}
.friend .mark{height:80px;display:flex;align-items:center;justify-content:center;gap:10px;font-family:'Raleway',sans-serif;font-weight:600;font-size:26px;color:#9ab0c4}
.friend .mark i{width:14px;height:14px;border-radius:50%;background:#cdd8e2}
.friend p{font-size:12px;line-height:19px;margin-top:10px}

/* footer */
.site-footer{top:4853px;height:79px;background:var(--dark)}
.site-footer p{position:absolute;left:100px;top:30px;color:#bbb;font-size:12px}
.social{position:absolute;right:100px;top:22px;display:flex;gap:10px}
.social i{width:34px;height:34px;border-radius:50%;border:2px solid #aaa;display:block}
</style>
</head>
<body>

<header class="site-header">
  <div class="abs brand"><span class="brand-dot"></span><span class="brand-name">T.O.R.U ENTERTAINMENT</span></div>
  <nav class="abs nav">
    <span class="active">HOME</span><span>WHAT WE DO</span><span>ABOUT US</span><span>WHY HIRE T.O.R.U</span><span>COUPLES</span><span>GALLERY</span><span>QUOTE</span><span>CONTACT</span><span>OUR BUDDIES</span>
    <svg width="14" height="14" viewBox="0 0 14 14"><circle cx="6" cy="6" r="4.5" fill="none" stroke="#2b2b2b" stroke-width="2"/><line x1="9.5" y1="9.5" x2="13" y2="13" stroke="#2b2b2b" stroke-width="2"/></svg>
  </nav>
</header>

<section class="hero" role="img" aria-label="Bride and groom dancing at a wedding reception">
  <svg class="arrow" style="left:50px;top:220px" viewBox="0 0 30 30"><polyline points="20,4 9,15 20,26" fill="none" stroke="#fff" stroke-width="3"/></svg>
  <svg class="arrow" style="right:50px;top:220px" viewBox="0 0 30 30"><polyline points="10,4 21,15 10,26" fill="none" stroke="#fff" stroke-width="3"/></svg>
  <h1>Getting rid the earth of boring weddings!</h1>
  <p>Our passion is to create every moment to deliver a truly one-of-a-kind wedding celebration that<br>you and your guests will love and remember, making your day memorable for many years.</p>
</section>

<section class="what">
  <h2 class="title abs" style="top:55px">WHAT WE DO</h2>
  <div class="service" style="left:100px">
    <div class="service-circle" role="img" aria-label="Master of ceremonies speaking at a reception" style="background:linear-gradient(150deg,#3a2a4a,#a2577a 60%,#e0a26c)">
      <div class="service-band" style="background:rgba(224,71,141,.85)">Wedding Master of Ceremonies</div>
    </div>
    <p>Master of Ceremonies Liesel will act as MC, entertainer, singer and the peacemaker of the celebration. She will be working</p>
    <div class="readmore">READ MORE &gt;&gt;</div>
  </div>
  <div class="service" style="left:450px">
    <div class="service-circle" role="img" aria-label="DJ mixing at the decks" style="background:linear-gradient(150deg,#7a1c2a,#c8343c 55%,#2b2b2b)">
      <div class="service-band" style="background:rgba(201,162,39,.9)">Wedding DJ</div>
    </div>
    <p>DJ Orin will look after the music element of your wedding entertainment. Your guests won't want to leave the dance floor as the perfect mix</p>
    <div class="readmore">READ MORE &gt;&gt;</div>
  </div>
  <div class="service" style="left:800px">
    <div class="service-circle" role="img" aria-label="Guests celebrating at a party" style="background:linear-gradient(150deg,#c99a7a,#e7c7a8 50%,#7a4c3a)">
      <div class="service-band" style="background:rgba(77,195,205,.9)">Extensive Wedding Party Pre-Planning</div>
    </div>
    <p>We'll spend on average 30 hours to help make your wedding celebration the best it can be. Together we'll think about what represents you</p>
    <div class="readmore">READ MORE &gt;&gt;</div>
  </div>
</section>

<section class="about" role="img" aria-label="Decorated wedding reception hall">
  <svg class="abs" style="left:0;top:0" width="1200" height="537" viewBox="0 0 1200 537">
    <polygon points="0,0 280,0 600,270 263,537 0,537" fill="#f6f3ef" opacity=".95"/>
    <polygon points="1200,0 920,0 600,270 937,537 1200,537" fill="#f6f3ef" opacity=".95"/>
  </svg>
  <h2 class="title abs about-title">ABOUT US</h2>
  <p class="abs about-lead">First off a big thanks for enquiring about our services<br>and being interested in what we're all about.</p>
  <div class="person" style="left:100px">
    <h3>MC Liesel</h3>
    <p>Liesel is a professional Wedding Master of Ceremonies, entertainer and a singer. She has a Master of Arts' degree in Communication and a Bachelor's degree in</p>
    <p>Theatre Studies. Orin says that working with Liesel is a lot of fun! She is passionate, creative and entertaining. She bosses him around a little though, but he doesn't mind that at all. "Happy wife - happy life!", he wisely notes.</p>
  </div>
  <div class="portrait" role="img" aria-label="Portrait of MC Liesel" style="left:447px;background:linear-gradient(#e6b9a0,#9a4a3a)"></div>
  <div class="portrait" role="img" aria-label="Portrait of DJ Orin" style="left:603px;background:linear-gradient(#b8c3cc,#3a4a5a)"></div>
  <div class="person" style="left:830px;width:290px">
    <h3>DJ Orin</h3>
    <p>Orin became DJ and a sound engineer, after meeting Liesel. Before he is a computer guru with Master and Bachelor's degrees in IT, and he loves all things sound</p>
    <p>and music. Liesel says that it's so cool to work with Orin. They're always on the same page and well prepared, which makes everything run smoothly. "Weddings and parties are the only places where we kiss on duty."</p>
  </div>
</section>

<section class="why">
  <h2 class="title abs" style="top:60px">WHY HIRE T.O.R.U?</h2>
  <p class="abs why-sub">TO CREATE THE BEST ATMOSPHERE AND GIVE YOU A PARTY LIKE NO OTHER!</p>
  <span class="ring" style="left:50px;top:250px"></span>
  <span class="ring" style="right:50px;top:250px"></span>
  <svg class="abs" style="left:58px;top:258px" width="22" height="22" viewBox="0 0 22 22"><polyline points="14,4 7,11 14,18" fill="none" stroke="#777" stroke-width="2.5"/></svg>
  <svg class="abs" style="right:58px;top:258px" width="22" height="22" viewBox="0 0 22 22"><polyline points="8,4 15,11 8,18" fill="none" stroke="#777" stroke-width="2.5"/></svg>
  <div class="reason" style="left:100px">
    <svg class="icon" viewBox="0 0 100 100"><path d="M50 88 C20 64 8 48 8 32 C8 18 19 10 30 10 C40 10 47 16 50 24 C53 16 60 10 70 10 C81 10 92 18 92 32 C92 48 80 64 50 88Z" fill="#e0478d"/></svg>
    <h4>Passion</h4>
    <p>Our true passion is to create a stress free and fun environment for our brides &amp; grooms. Your wedding day</p>
    <div class="readmore">READ MORE &gt;&gt;</div>
  </div>
  <div class="reason" style="left:365px">
    <div class="icon" role="img" aria-label="Pink clip-art of a couple holding hands" style="background:linear-gradient(#f3b6d2,#e0478d);border-radius:12px;opacity:.85"></div>
    <h4>Emotional connection</h4>
    <p>Our true passion is to create a stress free and fun environment for our brides &amp; grooms. Your wedding day</p>
    <div class="readmore">READ MORE &gt;&gt;</div>
  </div>
  <div class="reason" style="left:620px">
    <svg class="icon" viewBox="0 0 100 100"><path d="M34 20 L84 10 L84 66" fill="none" stroke="#e0478d" stroke-width="8"/><line x1="34" y1="20" x2="34" y2="76" stroke="#e0478d" stroke-width="8"/><ellipse cx="24" cy="78" rx="14" ry="10" fill="#e0478d"/><ellipse cx="74" cy="68" rx="14" ry="10" fill="#e0478d"/></svg>
    <h4>Creativity</h4>
    <p>Our true passion is to create a stress free and fun environment for our brides &amp; grooms. Your wedding day</p>
    <div class="readmore">READ MORE &gt;&gt;</div>
  </div>
  <div class="reason" style="left:870px">
    <div class="icon" role="img" aria-label="Pink clip-art of a megaphone" style="background:linear-gradient(#f3b6d2,#e0478d);border-radius:50%;opacity:.85"></div>
    <h4>Professional in every way</h4>
    <p>Our true passion is to create a stress free and fun environment for our brides &amp; grooms. Your wedding day</p>
    <div class="readmore">READ MORE &gt;&gt;</div>
  </div>
</section>

<section class="couples" role="img" aria-label="Couple on their wedding day under a gold tint">
  <svg class="abs" style="left:60px;top:200px" width="24" height="24" viewBox="0 0 24 24"><polyline points="15,4 7,12 15,20" fill="none" stroke="#fff" stroke-width="3"/></svg>
  <svg class="abs" style="right:60px;top:200px" width="24" height="24" viewBox="0 0 24 24"><polyline points="9,4 17,12 9,20" fill="none" stroke="#fff" stroke-width="3"/></svg>
  <h2 class="title abs">OUR HAPPY COUPLES</h2>
  <div class="abs avatar" role="img" aria-label="Portrait of the happy couple"></div>
  <p class="abs quote">"Dear Liesel and Orin, thank you for the wonderful entertainment you provided at our wedding. Even two months later friends and relatives still are raving about the wonderful evening and the equipment your music inspired. You are very talented. We'll definitely recommend your services to family and friends. You're professional, organised and lots of fun. Thank you for making our wedding day so special!"</p>
  <p class="abs signed">- LOVE, MIRA &amp; TOMAS!</p>
</section>

<section class="gallery">
  <h2 class="title abs">GALLERY</h2>
  <div class="tile" role="img" aria-label="First dance under blue lights" style="left:100px;top:148px;height:237px;background:linear-gradient(135deg,#3b3a8a,#b58ad8 60%,#f0d7f0)"></div>
  <div class="tile" role="img" aria-label="Couple with sparklers on the dance floor" style="left:437px;top:148px;height:237px;background:linear-gradient(135deg,#2a2a35,#d7c7b0 55%,#8c6a55)"></div>
  <div class="tile" role="img" aria-label="DJ hands on the mixer" style="left:774px;top:148px;height:237px;background:linear-gradient(135deg,#1e1a2a,#c8843a 55%,#6a2a6a)"></div>
  <div class="tile" role="img" aria-label="Tiered wedding cake with flowers" style="left:100px;top:401px;height:247px;background:linear-gradient(135deg,#6a4a20,#e8c36a 55%,#f7efe0)"></div>
  <div class="tile" role="img" aria-label="Guests dancing under purple lights" style="left:437px;top:401px;height:247px;background:linear-gradient(135deg,#1c2a6a,#5a7ad8 55%,#e0e6f5)"></div>
  <div class="tile" role="img" aria-label="Bride and groom dancing with guests" style="left:774px;top:401px;height:247px;background:linear-gradient(135deg,#2a3a2a,#a7b8a0 55%,#f0ede5)"></div>
  <div class="abs btn-outline">VIEW MORE &gt;&gt;</div>
</section>

<section class="instant">
  <h2 class="title abs">INSTANT QUOTE</h2>
  <div class="abs includes">
    <h5>OUR WEDDING PACKAGE INCLUDES:</h5>
    <ul>
      <li><svg class="tick" viewBox="0 0 16 16"><circle cx="8" cy="8" r="8" fill="#fff"/><polyline points="4,8 7,11 12,5" fill="none" stroke="#e0478d" stroke-width="2"/></svg>Liesel - Professional Master of Ceremonies/Interactive Entertainer</li>
      <li><svg class="tick" viewBox="0 0 16 16"><circle cx="8" cy="8" r="8" fill="#fff"/><polyline points="4,8 7,11 12,5" fill="none" stroke="#e0478d" stroke-width="2"/></svg>Orin - Professional DJ/Sound Engineer</li>
      <li><svg class="tick" viewBox="0 0 16 16"><circle cx="8" cy="8" r="8" fill="#fff"/><polyline points="4,8 7,11 12,5" fill="none" stroke="#e0478d" stroke-width="2"/></svg>State of the Art Sound &amp; Lighting Music Equipment</li>
      <li><svg class="tick" viewBox="0 0 16 16"><circle cx="8" cy="8" r="8" fill="#fff"/><polyline points="4,8 7,11 12,5" fill="none" stroke="#e0478d" stroke-width="2"/></svg>Microphones for You &amp; Your Guests</li>
      <li><svg class="tick" viewBox="0 0 16 16"><circle cx="8" cy="8" r="8" fill="#fff"/><polyline points="4,8 7,11 12,5" fill="none" stroke="#e0478d" stroke-width="2"/></svg>Your Song Choices</li>
      <li><svg class="tick" viewBox="0 0 16 16"><circle cx="8" cy="8" r="8" fill="#fff"/><polyline points="4,8 7,11 12,5" fill="none" stroke="#e0478d" stroke-width="2"/></svg>Extensive Pre-Planning</li>
      <li><svg class="tick" viewBox="0 0 16 16"><circle cx="8" cy="8" r="8" fill="#fff"/><polyline points="4,8 7,11 12,5" fill="none" stroke="#e0478d" stroke-width="2"/></svg>Unlimited phone calls and emails</li>
      <li><svg class="tick" viewBox="0 0 16 16"><circle cx="8" cy="8" r="8" fill="#fff"/><polyline points="4,8 7,11 12,5" fill="none" stroke="#e0478d" stroke-width="2"/></svg>We're available 7 days a week</li>
      <li><svg class="tick" viewBox="0 0 16 16"><circle cx="8" cy="8" r="8" fill="#fff"/><polyline points="4,8 7,11 12,5" fill="none" stroke="#e0478d" stroke-width="2"/></svg>Equipment delivery, setup and packdown (total time of approx. 4 hrs)</li>
    </ul>
  </div>
  <div class="abs form-box">
    <h5>REQUEST FORM</h5>
    <div class="field">Event Location :<span class="select"></span></div>
    <div class="field">Event Duration :<span class="select"></span></div>
    <div class="field">Number of guests :<span class="select"></span></div>
    <div class="btn-gold">GET INSTANT QUOTE</div>
  </div>
</section>

<section class="contact">
  <h2 class="title abs">CONTACT US</h2>
  <div class="abs contact-info">
    <b>We'd love to hear from you!</b>
    <p>Contact us on <span class="phone">0400 555 172</span> to arrange a time to get together, chat about ideas and to learn more. With our passion combined, we can create something truly memorable and totally you.</p>
    <div class="contact-line"><span><i></i>hello@toru-events.example</span><span><i></i>www.toru-events.example</span></div>
    <p>Or please fill in your details in the 'Contact us' form and we'll contact you shortly.</p>
  </div>
  <div class="abs contact-form">
    <label>Your Name (Required)</label><div class="input"></div>
    <label>Your Telephone (Required)</label><div class="input"></div>
    <label>Your Email (Required)</label><div class="input"></div>
    <label>Subject</label><div class="input"></div>
    <label>Message</label><div class="area"></div>
    <div style="position:relative;height:40px;margin-top:10px"><div class="abs send">SEND</div></div>
  </div>
</section>

<section class="friends">
  <h2 class="title abs">OUR TRUSTED FRIENDS</h2>
  <div class="friend" style="left:90px">
    <div class="mark"><i></i>Lumen Vale</div>
    <p>We worked with them at many weddings and events in our city, and they are wonderful photographers to work with</p>
  </div>
  <div class="friend" style="left:440px">
    <div class="mark" style="color:#c9a36a"><i></i>Petal Row</div>
    <p>They specialise in floral arrangements for weddings. She is a true floral guru, and just a beautiful lady.</p>
  </div>
  <div class="friend" style="left:790px">
    <div class="mark" style="color:#aaa">Brassline Music</div>
    <p>Brassline is an acclaimed professional saxophone player. We absolutely love him!</p>
  </div>
</section>

<footer class="site-footer">
  <p>Copyright © 2016, T.O.R.U. All rights reserved.</p>
  <div class="social"><i></i><i></i><i></i><i></i></div>
</footer>

</body>
</html>
```